BrindleStaffing Business Card Design

We are a staffing company finding positions for dedicated nurses and physicians.

Target Market(s)

Business Professionals

Industry/Entity Type

Staffing

Contact Information for Business Card

Gordon Pratley
Chairman
417 39th Avenue South
SAINT PETERSBURG FL 33712
813-555-4172 Mobile
813-555-8036 Fax
gpratley@brindlestaffing.com
www.brindlestaffing.com

Font styles to use
Sans Serif

Colors
fbee3e
f04a50
f37122

Requirements
Must have
• Logo Attached, see colors below. We'd like to see Yellow, Orange and Red.

```html
<!DOCTYPE html>
<html lang="en">
<head>
<meta charset="utf-8">
<title>BrindleStaffing Business Card</title>
<link rel="stylesheet" href="https://fonts.googleapis.com/css2?family=Open+Sans:wght@400;600;700&display=swap">
<style>
  :root {
    --backdrop: #1b1b1d;
    --card: #000000;
    --yellow: #fbee3e;
    --orange: #f37122;
    --red: #f04a50;
    --white: #f2f2f2;
    --rule: #6a6a6a;
  }
  * { margin: 0; padding: 0; box-sizing: border-box; }
  html, body {
    width: 1200px; height: 960px; overflow: hidden;
    background: var(--backdrop);
    font-family: "Open Sans", Arial, sans-serif;
  }
  .stage { position: relative; width: 1200px; height: 960px; }
  .card {
    position: absolute; left: 250px; width: 700px; height: 400px;
    background: var(--card);
    box-shadow: 0 18px 40px rgba(0,0,0,.55);
    overflow: hidden;
  }
  .card--back { top: 50px; }
  .card--front { top: 510px; }

  .brand {
    display: flex; align-items: center; gap: 14px;
    font-weight: 700; color: var(--orange);
    letter-spacing: -0.5px; white-space: nowrap;
  }
  .brand__dot {
    width: 22px; height: 22px; border-radius: 50%;
    background: var(--yellow);
  }

  .card--back .brand {
    position: absolute; left: 0; right: 0; top: 130px;
    justify-content: center; font-size: 54px;
  }
  .card--back .site-url {
    position: absolute; left: 0; right: 0; top: 232px;
    text-align: center; color: var(--white);
    font-size: 19px; letter-spacing: 2px;
  }
  .site-url__name { color: var(--yellow); font-weight: 700; }
  .site-url__name b { color: var(--orange); font-weight: 700; }

  .card--front .brand {
    position: absolute; right: 80px; top: 60px; font-size: 48px;
  }
  .details {
    position: absolute; left: 0; right: 0; top: 180px;
    display: flex; align-items: stretch;
  }
  .person { width: 330px; padding-right: 24px; text-align: right; }
  .person__name { color: var(--orange); font-weight: 700; font-size: 20px; }
  .person__title { color: var(--yellow); font-size: 17px; margin-bottom: 8px; }
  .person__address { color: var(--white); font-size: 15px; line-height: 1.35; }
  .divider { width: 1px; background: var(--rule); }
  .contact { list-style: none; padding-left: 22px; }
  .contact__item {
    display: flex; align-items: center; gap: 12px;
    color: var(--white); font-size: 17px; line-height: 1; margin-bottom: 14px;
  }
  .contact__item:last-child { margin-bottom: 0; }
  .contact__label { color: var(--yellow); font-size: 14px; }
  .contact__item svg { width: 16px; height: 16px; flex: none; }

  .stripe {
    position: absolute; left: 0; right: 0; bottom: 0; height: 12px;
    display: flex;
  }
  .stripe__seg { height: 100%; }
  .stripe__seg--yellow { background: var(--yellow); width: 27%; }
  .stripe__seg--orange { background: var(--orange); width: 30%; }
  .stripe__seg--red { background: var(--red); width: 43%; }
</style>
</head>
<body>
<div class="stage">

  <section class="card card--back">
    <div class="brand"><span class="brand__dot"></span>BrindleStaffing</div>
    <p class="site-url">www.<span class="site-url__name">brindle<b>staffing</b></span>.com</p>
  </section>

  <section class="card card--front">
    <div class="brand"><span class="brand__dot"></span>BrindleStaffing</div>

    <div class="details">
      <div class="person">
        <p class="person__name">Gordon Pratley</p>
        <p class="person__title">Chairman</p>
        <p class="person__address">417 39th Avenue South<br>Saint petersburg fl 33712</p>
      </div>
      <div class="divider"></div>
      <ul class="contact">
        <li class="contact__item">
          <svg viewBox="0 0 16 16" aria-hidden="true"><circle cx="8" cy="8" r="7" fill="none" stroke="#f37122" stroke-width="1.4"/><path d="M5.5 4.5l1.5 1.5-1 1c.6 1.3 1.6 2.3 2.9 2.9l1-1 1.5 1.5-1.2 1.2c-2.7-.6-4.8-2.7-5.4-5.4z" fill="#f37122"/></svg>
          813-555-4172 <span class="contact__label">Mobile</span>
        </li>
        <li class="contact__item">
          <svg viewBox="0 0 16 16" aria-hidden="true"><g fill="#f37122"><rect x="4" y="1.5" width="8" height="4"/><rect x="1.5" y="6" width="13" height="6" rx="1"/><rect x="4" y="10" width="8" height="4.5" fill="#000" stroke="#f37122" stroke-width="1.2"/></g></svg>
          813-555-8036 <span class="contact__label">Fax</span>
        </li>
        <li class="contact__item">
          <svg viewBox="0 0 16 16" aria-hidden="true"><rect x="1.5" y="3.5" width="13" height="9" rx="1" fill="#f37122"/><path d="M1.5 4l6.5 5 6.5-5" fill="none" stroke="#000" stroke-width="1.2"/></svg>
          gpratley@brindlestaffing.com
        </li>
        <li class="contact__item">
          <svg viewBox="0 0 16 16" aria-hidden="true"><g fill="none" stroke="#f37122" stroke-width="1.3"><circle cx="8" cy="8" r="6.5"/><ellipse cx="8" cy="8" rx="3" ry="6.5"/><path d="M1.5 8h13M2.5 5h11M2.5 11h11"/></g></svg>
          www.brindlestaffing.com
        </li>
      </ul>
    </div>

    <div class="stripe">
      <span class="stripe__seg stripe__seg--yellow"></span>
      <span class="stripe__seg stripe__seg--orange"></span>
      <span class="stripe__seg stripe__seg--red"></span>
    </div>
  </section>

</div>
</body>
</html>
```